Custom Manufacturing Company square space website design

I own a custom manufacturing company that uses precision cutting technology to manufacture project components over a couple industries. We have an industrial CNC router and state of the art edge bander and cut a lot of cabinetry components for cabinet shops, builders, closet companies, ect. We offer design and assembly for any cabinetry or can build cabinets to spec. We also cut components for other industries out of wood, plastics, acryclics, ect. We offer design engineering services, product development protype services. we have a 3D printer farm. We want our communicate trust, dependability, and the value we place on client relationships.

We essentially want a credibility website. Landing page and drops downs for services we offer, capabilites, about us, contact

```html
<!DOCTYPE html>
<html lang="en">
<head>
<meta charset="utf-8">
<title>Northgate Precision CNC</title>
<link href="https://fonts.googleapis.com/css2?family=Exo+2:wght@600;700&family=Poppins:wght@400;500;600&display=swap" rel="stylesheet">
<style>
:root{
  --gold:#d9a348;
  --ink:#111216;
  --ink-2:#16171c;
  --ink-3:#1c1d22;
  --white:#ffffff;
  --muted:#b9bbc2;
  --line:#2a2c33;
}
*{margin:0;padding:0;box-sizing:border-box}
html,body{width:1200px;height:3521px;overflow:hidden;background:var(--ink)}
body{position:relative;font-family:'Poppins',sans-serif;color:var(--white)}
.abs{position:absolute}
.heading{font-family:'Exo 2',sans-serif;font-weight:700;color:var(--white);text-transform:uppercase;letter-spacing:-.5px;white-space:nowrap}
.underline{position:absolute;height:12px;border:4px solid var(--gold);border-top:none}
.btn{position:absolute;display:flex;align-items:center;justify-content:center;gap:14px;background:var(--gold);color:var(--white);font-family:'Exo 2',sans-serif;font-weight:600;font-size:15px;text-transform:uppercase;text-decoration:none;white-space:nowrap}
.btn svg{width:22px;height:10px}
.body-text{font-size:16.5px;line-height:30px;color:var(--muted);text-align:justify}

/* header */
.site-header{left:0;top:0;width:1200px;height:86px;border-bottom:1px solid rgba(255,255,255,.35);z-index:3}
.brand{left:128px;top:34px;font-family:'Poppins',sans-serif;font-weight:500;font-size:14px;letter-spacing:3px;color:var(--white);display:flex;align-items:center;gap:10px;white-space:nowrap}
.brand-mark{width:14px;height:14px;border:2px solid var(--white)}
.nav{right:100px;top:0;display:flex;height:86px;font-family:'Exo 2',sans-serif;font-weight:700;font-size:16px}
.nav a{color:var(--white);text-decoration:none;padding:0 16px;display:flex;align-items:center}
.nav a.active{background:var(--gold)}

/* hero */
.hero{left:0;top:0;width:1200px;height:597px;background:linear-gradient(135deg,#4b5160 0%,#353944 45%,#565b66 75%,#8a8d93 100%)}
.hero-shade{left:154px;top:176px;width:893px;height:316px;background:rgba(40,42,48,.72)}
.corner{position:absolute;border:5px solid var(--gold)}
.hero-title{left:0;width:1200px;top:236px;text-align:center;font-size:60px}
.hero-text{left:195px;width:810px;top:348px;text-align:center;font-size:15.5px;line-height:30px}

/* about */
.about{left:0;top:597px;width:1200px;height:749px;background:var(--ink)}
.photo{position:absolute}

/* services */
.services{left:0;top:1346px;width:1200px;height:690px;background:var(--ink-2)}
.card-overlay{position:absolute;display:flex;flex-direction:column;align-items:center;justify-content:center;text-align:center;padding:0 40px;color:#2a2218}
.card-overlay h3{font-family:'Exo 2',sans-serif;font-weight:600;font-size:14px;text-transform:uppercase;margin-bottom:10px}
.card-overlay p{font-size:13px;line-height:23px;color:#fff7e6}

/* capabilities */
.capabilities{left:0;top:2036px;width:1200px;height:602px;background:linear-gradient(180deg,#101116,#17181d)}

/* contact */
.contact{left:0;top:2638px;width:1200px;height:553px;background:#222327}
.contact-panel{left:641px;top:2638px;width:447px;height:613px;background:var(--white);z-index:2}
.field{position:absolute;left:44px;width:354px;border-bottom:1px solid #333;font-size:16.5px;color:#333;padding-bottom:10px}

/* footer */
.footer{left:0;top:3191px;width:1200px;height:274px;background:var(--ink)}
.footer-nav{display:flex;gap:32px;font-family:'Exo 2',sans-serif;font-weight:700;font-size:16px;white-space:nowrap}
.social{display:flex;gap:22px}
.social span{width:14px;height:14px;border-radius:50%;border:2px solid var(--gold)}
.copyright{left:0;top:3465px;width:1200px;height:56px;background:#1d1e23;font-size:15px}
</style>
</head>
<body>

<!-- Hero -->
<section class="abs hero" role="img" aria-label="Photo of a dark modern kitchen with grey cabinetry and brass pendant lights"></section>
<header class="abs site-header">
  <div class="abs brand"><span class="brand-mark"></span>NORTHGATE CNC</div>
  <nav class="abs nav">
    <a class="active" href="#">HOME</a><a href="#">ABOUT US</a><a href="#">SERVICES WE OFFER</a><a href="#">CAPABILITIES</a><a href="#">CONTACT</a>
  </nav>
</header>
<div class="abs hero-shade"></div>
<div class="corner" style="left:154px;top:176px;width:136px;height:316px;border-right:none"></div>
<div class="corner" style="left:902px;top:176px;width:145px;height:316px;border-left:none"></div>
<h1 class="abs heading hero-title">Welcome to Northgate CNC</h1>
<div class="underline" style="left:540px;top:317px;width:124px"></div>
<p class="abs hero-text">Lorem ipsum dolor sit amet, consectetur adipiscing elit, sed do eiusmod tempor incididunt ut labore et dolore magna aliqua. Ut enim ad minim veniam, quis nostrud exercitation ullamco</p>
<a class="btn" style="left:533px;top:432px;width:167px;height:39px">Get Started<svg viewBox="0 0 22 10"><path d="M0 5h19M15 1l5 4-5 4" stroke="#fff" stroke-width="2" fill="none"/></svg></a>

<!-- About -->
<section class="abs about"></section>
<div class="photo" style="left:111px;top:737px;width:381px;height:362px;background:linear-gradient(135deg,#e6d6bc,#b08654 60%,#7d5a36)" role="img" aria-label="Photo of light wood stair cabinetry"></div>
<div class="photo" style="left:191px;top:843px;width:382px;height:362px;background:linear-gradient(160deg,#e8e4de 0%,#4a4036 40%,#2c2520 75%,#8a7868 100%)" role="img" aria-label="Photo of a walk-in closet with dark wood island"></div>
<h2 class="abs heading" style="left:646px;top:728px;font-size:40px">About Us</h2>
<div class="underline" style="left:670px;top:779px;width:123px"></div>
<p class="abs body-text" style="left:646px;top:843px;width:443px">Sed ut perspiciatis unde omnis iste natus error sit voluptatem accusantium doloremque laudantium, totam rem aperiam, eaque ipsa quae ab illo inventore veritatis et quasi architecto beatae vitae dicta sunt explicabo. Nemo enim ipsam voluptatem quia voluptas sit aspernatur aut odit aut fugit, sed quia consequuntur magni dolores eos qui ratione voluptatem sequi nesciunt. Neque porro quisquam est, qui dolorem ipsum quia dolor sit amet, consectetur.</p>
<a class="btn" style="left:644px;top:1160px;width:165px;height:41px">Read More<svg viewBox="0 0 22 10"><path d="M0 5h19M15 1l5 4-5 4" stroke="#fff" stroke-width="2" fill="none"/></svg></a>

<!-- Services -->
<section class="abs services"></section>
<h2 class="abs heading" style="left:0;width:1200px;text-align:center;top:1446px;font-size:40px">Services We Offer</h2>
<div class="underline" style="left:538px;top:1498px;width:124px"></div>
<p class="abs" style="left:220px;width:760px;top:1553px;text-align:center;font-size:16.5px;line-height:30px;color:var(--muted)">Sed ut perspiciatis unde omnis iste natus error sit voluptatem accusantium doloremque laudantium, totam rem aperiam, eaque ipsa quae ab illo inventore veritatis et quasi architecto beatae vitae dicta sunt explicabo.</p>
<div class="photo" style="left:111px;top:1703px;width:310px;height:227px;background:linear-gradient(135deg,#e7b863,#d09a43)" role="img" aria-label="Photo of a warm lit wooden walk-in closet"></div>
<div class="card-overlay" style="left:111px;top:1703px;width:310px;height:227px">
  <h3>Lorem ipsum dolor sit amet</h3>
  <p>Lorem ipsum dolor sit amet, consectetur adipiscing elit, sed do nostrud exercitation ullamco</p>
</div>
<div class="photo" style="left:447px;top:1703px;width:309px;height:227px;background:linear-gradient(135deg,#f1ece6,#c9a98c 50%,#e9e2da)" role="img" aria-label="Photo of an open wardrobe with colourful clothes"></div>
<div class="photo" style="left:780px;top:1703px;width:309px;height:227px;background:linear-gradient(135deg,#2e2c2a,#6b5b4a 50%,#3a3938)" role="img" aria-label="Photo of a dark closet with lit shelving and ottoman"></div>

<!-- Capabilities -->
<section class="abs capabilities"></section>
<h2 class="abs heading" style="left:118px;top:2140px;font-size:40px">Capabilities</h2>
<div class="underline" style="left:166px;top:2192px;width:124px"></div>
<p class="abs body-text" style="left:118px;top:2254px;width:481px">Sed ut perspiciatis unde omnis iste natus error sit voluptatem accusantium doloremque laudantium, totam rem aperiam, eaque ipsa quae ab illo inventore veritatis et quasi architecto beatae vitae dicta sunt explicabo. Nemo enim ipsam voluptatem quia voluptas sit aspernatur aut odit aut fugit, sed quia consequuntur magni dolores eos qui ratione voluptatem sequi nesciunt. Neque porro quisquam est, qui dolorem ipsum quia dolor sit amet, consectetur.</p>
<div class="photo" style="left:646px;top:2146px;width:554px;height:360px;background:linear-gradient(90deg,#8a6c4c,#d9d3c9 40%,#f1eee9 70%,#cbbfae)" role="img" aria-label="Video still of a bright pantry with wood shelving and a ladder"></div>
<svg class="abs" style="left:925px;top:2301px" width="50" height="50" viewBox="0 0 50 50"><circle cx="25" cy="25" r="25" fill="#d9a348" fill-opacity=".9"/><path d="M20 15l15 10-15 10z" fill="#fff"/></svg>

<!-- Contact -->
<section class="abs contact" role="img" aria-label="Faint dark world map background"></section>
<a class="btn" style="left:111px;top:2690px;width:244px;height:34px;background:#000">View Location Map<svg viewBox="0 0 22 10"><path d="M0 5h19M15 1l5 4-5 4" stroke="#fff" stroke-width="2" fill="none"/></svg></a>
<div class="abs heading" style="left:109px;top:3070px;font-size:72px;color:rgba(255,255,255,.1)">Contact Us</div>
<div class="abs contact-panel">
  <h2 class="abs heading" style="left:40px;top:76px;font-size:40px;color:#111">Contact Us</h2>
  <div class="underline" style="left:82px;top:128px;width:124px"></div>
  <div class="field" style="top:192px">Name</div>
  <div class="field" style="top:261px">Email</div>
  <div class="field" style="top:325px">Phone Number</div>
  <div class="field" style="top:393px">Message</div>
  <a class="btn" style="left:283px;top:477px;width:164px;height:39px">Submit<svg viewBox="0 0 22 10"><path d="M0 5h19M15 1l5 4-5 4" stroke="#fff" stroke-width="2" fill="none"/></svg></a>
</div>

<!-- Footer -->
<footer class="abs footer">
  <div class="abs brand" style="left:150px;top:60px"><span class="brand-mark"></span>NORTHGATE CNC</div>
  <p class="abs" style="left:114px;top:151px;width:250px;font-size:16px;line-height:25px">Sed ut perspiciatis unde omnis iste natus error sit voluptatem accusantium</p>
  <nav class="abs footer-nav" style="right:114px;top:113px"><span>HOME</span><span>ABOUT US</span><span>SERVICES WE OFFER</span><span>CAPABILITIES</span><span>CONTACT</span></nav>
  <div class="abs social" style="right:114px;top:172px"><span></span><span></span><span></span><span></span><span></span></div>
</footer>
<div class="abs copyright"><span class="abs" style="left:110px;top:18px">© 2023 Northgate Precision CNC</span></div>

</body>
</html>
```